Corvana Tongue Works, LLC

We need a business card that includes information about our business and conveys a reliable business that provides document translation services and interpreters for a variety of corporate and individual clients. We want to come across as professional, reliable, yet approachable. It should include the following on one side:

ESL / ENL Language Classes, Private Lessons, and Online Tutors
PLEXA Training and Testing
Translating & Interpreting Services
Contact us about Over-the-Phone Interpreting in over 200 languages
24/7/365
www.corvanatongue.example

The other side should include (555) 481-3062

Rhoda Pelling, President
482 Garnet Ave., Ste. 219
Indianapolis, IN 40917

Please add USA as part of the address. Also, please add rmpelling@corvanatongueworks.example as the e-mail address. Thank you.

Target Market(s)

Business professionals, their families, the international community

Industry/Entity Type

Business

Contact Information for Business Card

24/7/365
www.corvanatongue.example

(555) 481-3062

Rhoda Pelling, President
482 Garnet Ave., Ste. 219
Indianapolis, IN 40917
USA

Font styles to use
Sans Serif

Colors

Designer to choose colors to be used in the design.

Requirements
Must have
• See project description
• e-mail address and web address
• Phone number
Nice to have
• a globe
• physical address
Should not have
• Should not have the same color scheme as other agencies in our market in Indiana unless it is blue and black. No purple or yellow.

```html
<!DOCTYPE html>
<html lang="en">
<head>
<meta charset="utf-8">
<title>Corvana Tongue Works – Business Card</title>
<link rel="stylesheet" href="https://fonts.googleapis.com/css2?family=Amaranth&family=Cabin:wght@400&family=Mulish:wght@400&display=swap">
<style>
  :root {
    --canvas-bg: #dcd8d3;
    --card-bg: #f4f6f7;
    --card-edge: #ffffff;
    --brand-blue: #1a8db8;
    --ink: #2b2b2b;
    --swoosh: #2a2e33;
    --on-blue: #ffffff;
  }
  * { margin: 0; padding: 0; box-sizing: border-box; }
  html, body {
    width: 1200px; height: 1054px; overflow: hidden;
    background: var(--canvas-bg);
  }
  .card {
    position: absolute; left: 100px; top: 225px;
    width: 1000px; height: 604px;
    background: var(--card-bg);
    border: 2px solid var(--card-edge);
    overflow: hidden;
    box-shadow: 0 10px 30px rgba(0,0,0,0.18);
  }
  .card-shapes { position: absolute; inset: 0; width: 100%; height: 100%; }
  .name-tab {
    position: absolute; left: -24px; top: 76px;
    width: 48px; height: 102px; border-radius: 50%;
    background: var(--brand-blue);
  }
  .holder-name {
    position: absolute; left: 56px; top: 86px;
    font: 400 34px/44px "Amaranth", sans-serif; color: var(--brand-blue);
  }
  .holder-title {
    position: absolute; left: 56px; top: 136px;
    font: 400 22px/28px "Mulish", sans-serif; color: var(--ink);
  }
  .brand-mark {
    position: absolute; left: 466px; top: 55px;
    width: 204px; height: 204px; border-radius: 50%;
    background: var(--brand-blue);
  }
  .brand-name {
    position: absolute; left: 680px; top: 71px;
    font: 400 48px/63px "Cabin", sans-serif; color: var(--ink);
  }
  .brand-name .llc { font-size: 23px; }
  .address {
    position: absolute; left: 50px; top: 354px;
    font: 400 23px/39px "Mulish", sans-serif; color: var(--on-blue);
  }
  .contact-list {
    position: absolute; left: 50px; top: 444px; list-style: none;
    font: 400 23px/40px "Mulish", sans-serif; color: var(--on-blue);
  }
  .contact-list li { display: flex; align-items: center; gap: 20px; }
  .contact-list svg { width: 22px; height: 22px; flex: none; }
  .offerings {
    position: absolute; right: 50px; top: 428px; text-align: right;
    font: 400 14px/21px "Mulish", sans-serif; color: var(--on-blue);
  }
  .services {
    position: absolute; right: 50px; top: 494px; text-align: right;
    font: 400 24px/40px "Mulish", sans-serif; color: var(--on-blue);
  }
  .services .sep { margin: 0 6px 0 14px; }
</style>
</head>
<body>
<div class="card">
  <svg class="card-shapes" viewBox="0 0 787 475" preserveAspectRatio="none" aria-hidden="true">
    <path fill="var(--brand-blue)" d="M0 212 C140 196 290 228 440 296 C560 346 690 342 787 318 L787 475 L0 475 Z"/>
    <path fill="var(--swoosh)" d="M0 183 C190 150 330 232 470 286 C570 322 680 310 787 274 L787 284 C680 322 570 334 468 298 C330 246 190 168 0 200 Z"/>
    <path fill="var(--swoosh)" d="M392 308 C520 330 660 312 787 262 L787 292 C660 330 520 338 392 308 Z"/>
  </svg>

  <span class="name-tab"></span>
  <h1 class="holder-name">Rhoda Pelling</h1>
  <p class="holder-title">President</p>

  <span class="brand-mark"></span>
  <p class="brand-name">Corvana<br>Tongue<br>Works <span class="llc">LLC</span></p>

  <p class="address">482 Garnet Ave., Ste. 219<br>Indianapolis, IN 40917 USA</p>

  <ul class="contact-list">
    <li>
      <svg viewBox="0 0 24 24" fill="var(--on-blue)"><path d="M3 9c0-3 4-5 9-5s9 2 9 5l-1 2-4-1v-2c-3-1-5-1-8 0v2l-4 1zM6 13h12l2 7H4z"/></svg>
      (555) 481-3062
    </li>
    <li>
      <svg viewBox="0 0 24 24" fill="none" stroke="var(--on-blue)" stroke-width="2"><rect x="3" y="6" width="18" height="12"/><path d="M3 6l9 7 9-7"/></svg>
      rmpelling@corvanatongueworks.example
    </li>
    <li>
      <svg viewBox="0 0 24 24" fill="none" stroke="var(--on-blue)" stroke-width="1.8"><circle cx="12" cy="12" r="9"/><ellipse cx="12" cy="12" rx="4" ry="9"/><path d="M3 12h18M5 7h14M5 17h14"/></svg>
      www.corvanatongue.example
    </li>
  </ul>

  <p class="offerings">ESL / ENL Classes · Private Lessons · Online Tutors<br>PLEXA Training &amp; Testing · 24/7/365<br>Over-the-Phone Interpreting in 200+ Languages</p>

  <p class="services">Translating<span class="sep">«</span> Interpreting<span class="sep">«</span><br>Language Training<span class="sep">«</span></p>
</div>
</body>
</html>
```